New Business Card Design Project

I need a design for business cards, i am an electrical business called "Corvane Electrical and Communications" i need the cards to be double sided with the company logo on the back (attached) the front needs to say my company name, web site, email address, telephone number, and ABN number and electrical license number. I am open to different arrangements of the information but would like the background to be incorporating something electrical or something that looks smart. open to all additional ideas also.

The company colours are orange and grey see logo attached.

Business Name: Corvane Electrical and Communications
Website: corvaneelectricalandcomms.example.com.au
Email: brent@corvaneelectricalandcomms.example.com.au
Telephone(mobile): 0481209736
ABN: 71208349162
Lic No: 418273D

Target Market(s)

Business entities, Project Managers, Accounts, Clients

Industry/Entity Type

Electrician

Contact Information for Business Card

I need a design for business cards, i am an electrical business called "Corvane Electrical and Communications" i need the cards to be double sided with the company logo on the back (attached) the front needs to say my company name

Font styles to use
Serif
Sans Serif

Colors
f37122
5c5c5c

Requirements
Must have
• Must have the Logo on the back open to different ways of it being on the back but had in mind to keep it central but again open to other options
Nice to have
• A real modern cool background that is eye catching yet contemporary
Should not have
• No backgrounds of a light bulb or plug or anything like that

```html
<!DOCTYPE html>
<html lang="en">
<head>
<meta charset="utf-8">
<title>Corvane Electrical and Communications – Business Cards</title>
<link rel="stylesheet" href="https://fonts.googleapis.com/css2?family=Exo+2:wght@300;400;500&display=swap">
<style>
  :root {
    --backdrop: #8f9090;
    --card-dark: #4a4a4d;
    --card-light: #eeeeef;
    --band-light: #e4e4e6;
    --orange: #e69a1f;
    --grey-text: #5c5c5c;
    --light-text: #e6e6e8;
  }
  * { box-sizing: border-box; margin: 0; padding: 0; }
  html, body {
    width: 1105px; height: 1200px; overflow: hidden;
    background: var(--backdrop);
    font-family: "Exo 2", Arial, sans-serif;
  }
  .card {
    position: absolute; left: 180px; width: 746px; height: 427px; overflow: hidden;
  }
  .card-front { top: 119px; background: var(--card-dark); }
  .card-back { top: 637px; background: var(--card-light); }

  .front-brand {
    position: absolute; left: 52px; top: 150px; width: 290px;
    display: flex; align-items: center; gap: 14px;
  }
  .brand-dot {
    flex: none; width: 22px; height: 22px; border-radius: 50%; background: var(--orange);
  }
  .front-brand .brand-name {
    color: var(--light-text); font-weight: 500; font-size: 27px; line-height: 1.15;
  }

  .contact {
    position: absolute; left: 370px; top: 105px; color: var(--light-text);
  }
  .person-name {
    color: var(--orange); font-weight: 400; font-size: 28px; letter-spacing: 0.5px; line-height: 1;
  }
  .person-role {
    font-size: 19px; font-weight: 300; margin-top: 10px; letter-spacing: 0.3px;
  }
  .reg { font-size: 19px; font-weight: 300; margin-top: 14px; line-height: 1.4; letter-spacing: 0.3px; }
  .reg p + p { margin-top: 0; }
  .contact-list { list-style: none; margin-top: 10px; }
  .contact-list li {
    display: flex; align-items: center; gap: 10px; font-weight: 300; line-height: 1; height: 29px;
  }
  .contact-list .phone { font-size: 20px; letter-spacing: 0.5px; }
  .contact-list .email, .contact-list .web { font-size: 14.5px; }
  .contact-list svg { flex: none; width: 16px; height: 16px; fill: var(--orange); }

  .front-band {
    position: absolute; left: 0; bottom: 0; width: 100%; height: 31px;
    background: var(--band-light); border-top: 3px solid var(--orange);
  }

  .back-brand {
    position: absolute; left: 0; top: 0; width: 100%; height: 100%;
    display: flex; align-items: center; justify-content: center; gap: 20px;
  }
  .back-brand .brand-dot { width: 34px; height: 34px; }
  .back-brand .brand-name {
    color: var(--grey-text); font-weight: 500; font-size: 40px; line-height: 1.15; width: 360px;
  }
</style>
</head>
<body>
  <section class="card card-front" aria-label="Business card front">
    <div class="front-brand">
      <span class="brand-dot"></span>
      <span class="brand-name">Corvane Electrical and Communications</span>
    </div>

    <div class="contact">
      <h1 class="person-name">DANA WHITLOW</h1>
      <p class="person-role">CEO/FOUNDER</p>
      <div class="reg">
        <p>ABN: 71208349162</p>
        <p>Lic No: 418273D</p>
      </div>
      <ul class="contact-list">
        <li class="phone">
          <svg viewBox="0 0 16 16" aria-hidden="true"><path d="M4 0h8a1.5 1.5 0 0 1 1.5 1.5v13A1.5 1.5 0 0 1 12 16H4a1.5 1.5 0 0 1-1.5-1.5v-13A1.5 1.5 0 0 1 4 0zm0 2v10.5h8V2zm4 11.2a.9.9 0 1 0 0 1.8.9.9 0 0 0 0-1.8z"/></svg>
          0481209736
        </li>
        <li class="email">
          <svg viewBox="0 0 16 16" aria-hidden="true"><path d="M0 3h16v1.2L8 9 0 4.2zm0 2.6 8 4.8 8-4.8V13H0z"/></svg>
          brent@corvaneelectricalandcomms.example.com.au
        </li>
        <li class="web">
          <svg viewBox="0 0 16 16" aria-hidden="true"><path d="M8 0a8 8 0 1 0 0 16A8 8 0 0 0 8 0zm0 1.5c.9 0 1.9 1.6 2.3 4H5.7C6.1 3.1 7.1 1.5 8 1.5zM1.7 6.8h2.6a13 13 0 0 0 0 2.4H1.7a6.5 6.5 0 0 1 0-2.4zm4 0h4.6a11 11 0 0 1 0 2.4H5.7a11 11 0 0 1 0-2.4zm6 0h2.6a6.5 6.5 0 0 1 0 2.4h-2.6a13 13 0 0 0 0-2.4zM5.7 10.5h4.6c-.4 2.4-1.4 4-2.3 4s-1.9-1.6-2.3-4z"/></svg>
          corvaneelectricalandcomms.example.com.au
        </li>
      </ul>
    </div>

    <div class="front-band"></div>
  </section>

  <section class="card card-back" aria-label="Business card back">
    <div class="back-brand">
      <span class="brand-dot"></span>
      <span class="brand-name">Corvane Electrical and Communications</span>
    </div>
  </section>
</body>
</html>
```